Harvest Gateway Fellowship Ministries needs a fresh new web design

We are an up and coming multicultural church that aims to bring people into a life changing encounter with God. We need a fresh and inviting website in order to increase our internet presence and make us easier to connect with.
Here are some of the basic requirements for the site:
• Clearly displayed address, service times, and contact info
• A staff profile page
• An area for a calendar with upcoming events and their details
• Social media buttons
• Group pages for the different ministries (youth, children’s church, men, etc…)
• An area for donations and eCommerce
• A resources page for assorted media (podcasts, sermons, videos, etc.…)
• An area for prayer requests.

```html
<!DOCTYPE html>
<html lang="en">
<head>
<meta charset="utf-8">
<title>Groups – Harvest Gateway Fellowship Ministries</title>
<link href="https://fonts.googleapis.com/css2?family=Lato:ital,wght@0,300;0,400;0,700;1,400&display=swap" rel="stylesheet">
<style>
:root{
  --navy:#1d0f95;
  --navy-line:#3a2cb0;
  --gold:#e3bf0b;
  --gold-text:#d9b400;
  --ink:#333;
  --muted:#666;
  --soft:#f1f1f1;
  --foot-text:#b9b3ea;
  --white:#fff;
}
*{margin:0;padding:0;box-sizing:border-box}
html,body{width:1200px;height:1150px;overflow:hidden}
body{font-family:'Lato',sans-serif;color:var(--ink);background:var(--soft);position:relative}
a{color:inherit;text-decoration:none}
.topbar{position:absolute;top:0;left:0;width:1200px;height:40px;background:var(--navy);color:var(--white)}
.topbar .motto{position:absolute;left:100px;top:12px;font-size:13px}
.topbar .schedule-label{position:absolute;left:736px;top:12px;font-size:13px;padding-right:10px;border-right:1px solid var(--white);height:26px;top:7px;line-height:26px}
.topbar .schedule{position:absolute;left:932px;top:6px;font-size:11.5px;line-height:14px}
.header{position:absolute;top:40px;left:0;width:1200px;height:115px;background:var(--white)}
.brand{position:absolute;left:100px;top:20px;display:flex;align-items:center;gap:10px}
.brand-dot{width:48px;height:48px;border-radius:50%;background:var(--navy)}
.brand-name{font-size:19px;font-weight:700;color:var(--navy);line-height:22px;width:190px}
.info{position:absolute;top:24px;text-align:right;font-size:14px;color:var(--muted);line-height:16px}
.info h4{font-size:15px;color:#555;font-weight:700;margin-bottom:5px}
.info .more{font-size:12px;color:var(--gold-text);display:block;margin-top:2px}
.info.sep{padding-right:20px;border-right:2px solid #ddd;height:64px}
.social-head{position:absolute;left:1073px;top:29px;display:flex;flex-direction:column;gap:4px}
.social-head span,.social-foot span{display:block;border-radius:50%;background:#999}
.social-head span{width:27px;height:27px}
.nav{position:absolute;top:155px;left:0;width:1200px;height:41px;background:var(--gold);border-top:2px solid #d3b000}
.nav ul{list-style:none;display:flex;position:absolute;left:100px;top:10px;font-size:14px;color:#444}
.nav li{padding:0 25px;border-left:1px solid #c9a600;line-height:18px}
.nav li:first-child{border-left:none;padding-left:16px}
.banner{position:absolute;top:196px;left:0;width:1200px;height:100px;background:linear-gradient(90deg,#3b2410,#6a4a1e 30%,#8a6b2e 55%,#5a3e18 80%,#2e1c0c)}
.crumbs{position:absolute;left:100px;top:28px;color:var(--white);font-size:13px}
.banner h1{position:absolute;left:100px;top:44px;color:var(--white);font-size:26px;font-weight:700}
.verse{position:absolute;top:348px;left:0;width:1200px;text-align:center}
.verse blockquote{font-size:22px;font-weight:300;color:var(--muted)}
.verse cite{display:block;margin-top:6px;font-size:13px;color:#888}
.groups{position:absolute;top:449px;left:110px;display:flex;gap:34px}
.group{width:220px;text-align:center}
.group .photo{width:218px;height:160px;margin:0 auto;border:1px solid #ddd}
.group h3{margin-top:17px;font-size:18px;font-weight:400;color:var(--gold-text);text-transform:uppercase}
.group p{margin-top:8px;font-size:13px;line-height:19px;color:var(--muted)}
.group .btn{display:block;margin-top:24px;height:50px;border:2px solid var(--gold);line-height:46px;font-size:14px;color:var(--gold-text)}
.footer{position:absolute;top:848px;left:0;width:1200px;height:302px;background:var(--navy);color:var(--foot-text);font-size:13px}
.footer h5{font-size:19px;font-weight:300;color:#e8e6ff;margin-bottom:13px;text-transform:uppercase}
.col{position:absolute;top:42px;line-height:18px}
.contact-line{display:flex;align-items:center;gap:8px;font-size:14px;margin-top:4px}
.bullets{display:flex;gap:26px}
.bullets ul{list-style:none;line-height:24px}
.email-field{margin-top:8px;width:228px;height:34px;background:var(--white);border:1px solid #ccc;color:#aaa;padding-left:12px;line-height:32px}
.subscribe{margin-top:10px;width:93px;height:34px;background:var(--gold);color:var(--white);text-align:center;line-height:34px}
.social-foot{display:flex;gap:8px;margin-top:9px}
.social-foot span{width:32px;height:32px;background:#aaa4e0}
.rule{position:absolute;top:225px;left:100px;width:1000px;border-top:1px solid var(--navy-line)}
.copyright{position:absolute;top:242px;width:1200px;text-align:center;font-size:12px}
</style>
</head>
<body>
<div class="topbar">
  <div class="motto">A house of prayer for all nations, where the love, the presence and the power of God are real.</div>
  <div class="schedule-label">SUNDAY SERVICE SCHEDULE</div>
  <div class="schedule">09:00 A.M. | Sunday School<br>10:30 A.M. | Convergent Service</div>
</div>
<header class="header">
  <div class="brand"><span class="brand-dot"></span><span class="brand-name">Harvest Gateway Fellowship Ministries</span></div>
  <div class="info sep" style="right:606px"><h4>Donate</h4>Lorem Ipsum is simply<br>dummy text of the printing<a class="more" href="#">Donate Now »</a></div>
  <div class="info sep" style="right:324px"><h4>Request Prayer</h4>Lorem Ipsum is simply dummy text<br>of the printing and typesetting industry.<a class="more" href="#">Request Now »</a></div>
  <div class="info" style="right:168px"><h4>Address</h4>Harvest Gateway<br>City, Location<a class="more" href="#">Contact »</a></div>
  <div class="social-head"><span></span><span></span></div>
</header>
<nav class="nav"><ul>
  <li>Home</li><li>About</li><li>Staff Profile</li><li>News and Events</li><li>Worship &amp; Services</li><li>Groups</li><li>Shop</li><li>Resources</li><li>Contact</li>
</ul></nav>
<section class="banner" role="img" aria-label="Golden wheat field at dusk">
  <div class="crumbs">Home &gt; Groups</div>
  <h1>Groups</h1>
</section>
<div class="verse">
  <blockquote>“For where two or three are gathered in my name, there am I among them.”</blockquote>
  <cite>Matthew 18:20</cite>
</div>
<section class="groups">
  <article class="group"><div class="photo" role="img" aria-label="Young child playing with confetti" style="background:linear-gradient(135deg,#6a8a2a,#c9a86a,#d8568a)"></div><h3>Children’s Ministry</h3><p>Lorem Ipsum is simply dummy text of the printing and typesetting industry industry’s standard.</p><a class="btn" href="#">KNOW MORE</a></article>
  <article class="group"><div class="photo" role="img" aria-label="Women sitting together in a discussion circle" style="background:linear-gradient(135deg,#8a8f94,#cfc6b4,#5e5a55)"></div><h3>Ladies Ministry</h3><p>Lorem Ipsum is simply dummy text of the printing and typesetting industry industry’s standard.</p><a class="btn" href="#">KNOW MORE</a></article>
  <article class="group"><div class="photo" role="img" aria-label="Choir singing around a grand piano" style="background:linear-gradient(135deg,#6b3a1c,#2a2a2e,#a07a3a)"></div><h3>Music Ministry</h3><p>Lorem Ipsum is simply dummy text of the printing and typesetting industry industry’s standard.</p><a class="btn" href="#">KNOW MORE</a></article>
  <article class="group"><div class="photo" role="img" aria-label="Young people joining hands in a circle" style="background:linear-gradient(135deg,#9aa2b0,#c23a3a,#3a3e52)"></div><h3>Youth Ministry</h3><p>Lorem Ipsum is simply dummy text of the printing and typesetting industry industry’s standard.</p><a class="btn" href="#">KNOW MORE</a></article>
</section>
<footer class="footer">
  <div class="col" style="left:100px">
    <h5>Contact Us</h5>
    Harvest Gateway<br>Location, city<br>State Name, Country
    <div class="contact-line" style="margin-top:12px"><svg width="16" height="16" viewBox="0 0 16 16"><path d="M3 1l3 3-1.5 2c1 2 2.5 3.5 4.5 4.5L11 9l3 3-2 2C6 13 2 9 1 3z" fill="#b9b3ea"/></svg>+1 555-014-2290</div>
    <div class="contact-line"><svg width="16" height="12" viewBox="0 0 16 12"><rect x="0.5" y="0.5" width="15" height="11" fill="none" stroke="#b9b3ea"/><path d="M1 1l7 6 7-6" fill="none" stroke="#b9b3ea"/></svg>hello@harvestgateway.org</div>
  </div>
  <div class="col" style="left:321px">
    <h5>Communities We Serve</h5>
    <div class="bullets">
      <ul><li>• Lorem Ipsum</li><li>• Dummy Links</li><li>• More dummy</li><li>• Sample Text</li><li>• More samples</li></ul>
      <ul><li>• type text dummy</li><li>• Lorem Ipsum</li></ul>
    </div>
  </div>
  <div class="col" style="left:599px">
    <h5>Newsletter</h5>
    Enter your email below to get notified
    <div class="email-field">Your Email</div>
    <div class="subscribe">Subscribe</div>
  </div>
  <div class="col" style="left:877px">
    <h5>Connect With Us</h5>
    Stay connected for the latest updates at<br>Harvest Gateway Fellowship
    <div class="social-foot"><span></span><span></span></div>
  </div>
  <div class="rule"></div>
  <div class="copyright">Copyright © 2014. All rights reserved. Harvest Gateway.</div>
</footer>
</body>
</html>
```